Haulage company, lets use ruby red white and some 3rd color for web design. and Garvel Pryce Transport logo

Target Market(s)

Transport industry

Industry/Entity Type

transport

Number of Pages Required

2 page

Requirements
Must have
• Logo

```html
<!DOCTYPE html>
<html lang="en">
<head>
<meta charset="utf-8">
<title>Garvel Pryce Transport</title>
<link href="https://fonts.googleapis.com/css2?family=Montserrat:wght@600;700&family=Roboto:ital,wght@0,400;0,500;0,700;1,400&display=swap" rel="stylesheet">
<style>
:root{
  --ruby:#8b0a14;
  --ruby-deep:#5b0d22;
  --blush:#fdeef0;
  --ink:#1b1b1b;
  --text:#4a4a4a;
  --muted:#8a8a8a;
  --white:#ffffff;
  --night:#151213;
}
*{box-sizing:border-box;margin:0;padding:0}
html,body{width:1200px;height:3449px;overflow:hidden}
body{font-family:'Roboto',sans-serif;color:var(--text);background:var(--white);position:relative}
.abs{position:absolute}
h1,h2,h3,.brand{font-family:'Montserrat',sans-serif}
.accent{color:var(--ruby)}
.btn{position:absolute;display:flex;align-items:center;justify-content:center;gap:10px;color:#fff;font:700 14px 'Roboto',sans-serif;text-transform:uppercase;background:var(--ruby)}
.btn::after{content:"";position:absolute;left:10px;right:10px;bottom:-5px;height:2px;background:var(--ruby)}
.btn .dot{width:14px;height:14px;border-radius:50%;background:#fff;display:inline-flex;align-items:center;justify-content:center}
.btn .dot svg{width:8px;height:8px}

/* header */
.site-header{position:absolute;left:0;top:0;width:1200px;height:77px;background:#fff}
.brand{position:absolute;left:112px;top:18px;font-size:28px;font-weight:700;color:var(--ink)}
.nav{position:absolute;left:487px;top:28px;display:flex;gap:33px;font:500 14px 'Roboto',sans-serif;color:var(--ink)}
.nav .active{border-bottom:2px solid var(--ruby);padding-bottom:6px}
.call{position:absolute;left:904px;top:14px;width:185px;height:49px;background:var(--ruby-deep);color:#fff;display:flex;align-items:center}
.call .ico{width:38px;height:49px;background:var(--ruby);display:flex;align-items:center;justify-content:center}
.call .txt{padding-left:12px;line-height:1.2}
.call small{font-size:10px;font-weight:700;display:block}
.call b{font-size:15px}

/* hero */
.hero{position:absolute;left:0;top:77px;width:1200px;height:546px;background:linear-gradient(160deg,#9aa6b6 0%,#c9ccd0 30%,#6c6e6a 60%,#3f4438 100%)}
.hero svg.shade{position:absolute;left:0;top:0}
.follow{position:absolute;left:40px;top:165px;color:#fff;font-size:10px;font-weight:700;writing-mode:vertical-rl;transform:rotate(180deg)}
.follow-line{position:absolute;left:47px;top:240px;width:1px;height:62px;background:#fff}
.social-dot{position:absolute;left:43px;width:9px;height:9px;border-radius:2px;background:#fff}
.hero .kicker{position:absolute;left:107px;top:160px;color:#fff;font-size:28px;font-weight:700}
.hero h1{position:absolute;left:107px;top:201px;color:#fff;font-size:41px;font-weight:700}
.hero p{position:absolute;left:107px;top:268px;width:440px;color:#fff;font-size:14px;font-weight:700;line-height:23px}

/* about */
.about-band{left:0;top:889px;width:534px;height:328px;background:var(--ruby)}
.about-frame{left:264px;top:727px;width:300px;height:327px;border:2px solid var(--ruby)}
.about-photo{left:111px;top:743px;width:430px;height:405px;background:linear-gradient(180deg,#3f6aa8 0%,#8aa2c4 45%,#55534f 75%,#3a3a38 100%)}
.sec-title{position:absolute;font-size:40px;font-weight:700;color:var(--ink)}
.rule{position:absolute;width:36px;height:3px;background:var(--ruby)}
.about-copy{left:639px;top:869px;width:449px;font-size:15px;line-height:28.3px;text-align:justify}

/* services */
.services{left:0;top:1302px;width:1200px;height:521px;background:var(--blush)}
.svc{position:absolute;top:145px;width:315px;height:288px;display:flex;align-items:flex-end;justify-content:center;padding-bottom:38px;color:#fff;font:700 23px 'Montserrat',sans-serif}
.svc-a{left:112px;background:linear-gradient(180deg,#8e9aa8 0%,#c2b89e 45%,#7b7466 70%,#8a8a88 100%)}
.svc-c{left:775px;background:linear-gradient(180deg,#b8c4cf 0%,#dfe3e6 45%,#8e8e8c 75%,#a0a09c 100%)}
.svc-b{left:445px;background:#2a2326;box-shadow:0 6px 18px rgba(0,0,0,.35)}
.svc-b .panel{position:absolute;left:16px;top:16px;right:16px;bottom:16px;background:rgba(150,8,20,.92);display:flex;flex-direction:column;align-items:center;text-align:center;padding-top:28px}
.svc-b h3{font-size:23px;margin-top:22px}
.svc-b p{font:400 13px 'Roboto',sans-serif;line-height:20px;width:250px;margin-top:12px}

/* testimonials */
.tcard{position:absolute;top:2003px;width:457px;height:276px;background:#fff;box-shadow:0 0 14px rgba(0,0,0,.08)}
.tcard::before{content:"";position:absolute;left:-9px;right:9px;bottom:-13px;height:13px;background:#f2e1e3;z-index:-1}
.avatar{position:absolute;left:27px;top:36px;width:67px;height:57px;background:#f3d9dc}
.avatar i{position:absolute;left:5px;top:-5px;width:62px;height:57px;background:linear-gradient(180deg,#b8c7d6,#7b95b3)}
.tname{position:absolute;left:115px;top:44px;font:700 16px 'Montserrat',sans-serif;color:var(--ink)}
.trole{position:absolute;left:114px;top:69px;font-size:15px;color:var(--muted)}
.tquote{position:absolute;left:27px;top:112px;width:405px;font-size:15px;font-style:italic;line-height:27.5px;text-align:justify;color:#555}
.tmore{position:absolute;left:27px;top:227px;font-size:15px;font-weight:500;color:var(--ruby);text-decoration:underline}
.tarrow{position:absolute;top:2139px;width:29px;height:29px;border-radius:50%;display:flex;align-items:center;justify-content:center}

/* quote */
.quote{left:0;top:2391px;width:1200px;height:616px;background:linear-gradient(180deg,#9bb0c8 0%,#d8dde3 30%,#8c8a88 60%,#6f6c6a 100%)}
.field{position:absolute;background:#fff;color:#7a7a7a;font-size:14px;padding:12px 14px;display:flex;justify-content:space-between}
.field svg{width:12px;height:12px}

/* footer */
.fhead{position:absolute;top:3104px;font:700 19px 'Roboto',sans-serif;color:var(--ink)}
.frule{position:absolute;top:3138px;width:28px;height:2px;background:var(--ruby)}
.ftext{position:absolute;font-size:14px;line-height:24px;color:#666}
.fcontact{position:absolute;left:544px;display:flex;align-items:center;gap:17px;font-size:14px;color:#666}
.fcontact .pin{width:33px;height:33px;border-radius:50%;background:var(--ruby);display:flex;align-items:center;justify-content:center}
.qlinks{position:absolute;left:967px;top:3166px;list-style:none;font-size:14px;color:#666;line-height:30px}
.qlinks li::before{content:"»";color:var(--ruby);margin-right:20px}
.bottom-bar{left:0;top:3398px;width:1200px;height:51px;background:var(--ruby-deep)}
.bsoc{position:absolute;top:14px;width:28px;height:28px;border-radius:50%;background:var(--ruby);display:flex;align-items:center;justify-content:center}
.bsoc i{width:10px;height:10px;border-radius:2px;background:#fff}
</style>
</head>
<body>

<header class="site-header">
  <div class="brand">Garvel Pryce <span class="accent">Transport</span></div>
  <nav class="nav">
    <span class="active">Home</span><span>About Us</span><span>Services</span><span>Blog</span><span>Contact Us</span>
  </nav>
  <div class="call">
    <div class="ico"><svg width="16" height="16" viewBox="0 0 24 24"><path fill="#fff" d="M6.6 10.8a15 15 0 0 0 6.6 6.6l2.2-2.2a1 1 0 0 1 1-.25 11.4 11.4 0 0 0 3.6.57 1 1 0 0 1 1 1V20a1 1 0 0 1-1 1A17 17 0 0 1 3 4a1 1 0 0 1 1-1h3.5a1 1 0 0 1 1 1c0 1.25.2 2.45.57 3.57a1 1 0 0 1-.25 1z"/></svg></div>
    <div class="txt"><small>Call Us Today !</small><b>+1 555 010 4477</b></div>
  </div>
</header>

<section class="hero" role="img" aria-label="Refrigerated articulated truck driving on a motorway">
  <svg class="shade" width="1200" height="546"><polygon points="0,0 746,0 470,546 0,546" fill="rgba(110,10,40,0.78)"/></svg>
  <div class="follow">FOLLOW US</div>
  <div class="follow-line"></div>
  <span class="social-dot" style="top:322px"></span>
  <span class="social-dot" style="top:349px"></span>
  <span class="social-dot" style="top:375px"></span>
  <div class="kicker brand" style="left:107px;top:160px;font-size:28px;color:#fff">Welcome To</div>
  <h1>Garvel Pryce Transport</h1>
  <p>Lorem ipsum dolor sit amet, consectetur adipiscing elit, sed do eiusmod tempor incididunt ut labore et dolore magna aliqua.</p>
  <div class="btn" style="left:107px;top:335px;width:155px;height:48px;border:1px solid #fff">Get Started <span class="dot"><svg viewBox="0 0 10 10"><path d="M3 1l4 4-4 4" stroke="#8b0a14" stroke-width="2" fill="none"/></svg></span></div>
</section>

<div class="abs about-band"></div>
<div class="abs about-frame"></div>
<div class="abs about-photo" role="img" aria-label="Truck cab parked at dusk"></div>
<h2 class="sec-title" style="left:639px;top:792px">About <span class="accent">Us</span></h2>
<div class="rule" style="left:639px;top:848px"></div>
<p class="abs about-copy">Lorem ipsum dolor sit amet, consectetur adipiscing elit, sed do eiusmod tempor incididunt ut labore et dolore magna aliqua. Ut enim ad minim veniam, quis nostrud exercitation ullamco laboris nisi ut aliquip ex ea commodo consequat. Duis aute irure dolor in reprehenderit in voluptate velit esse cillum dolore eu fugiat nulla pariatur. Excepteur sint occaecat cupidatat non proident, sunt in culpa qui officia deserunt mollit anim id est laboru perspiciatis unde omnis iste natus error sit voluptatem accusantium doloremque laudantium, totam rem aperiam,</p>
<div class="btn" style="left:639px;top:1154px;width:148px;height:48px">Learn More <span class="dot"><svg viewBox="0 0 10 10"><path d="M3 1l4 4-4 4" stroke="#8b0a14" stroke-width="2" fill="none"/></svg></span></div>

<section class="abs services">
  <h2 class="sec-title" style="left:0;width:1200px;text-align:center;top:54px">Our <span class="accent">Services</span></h2>
  <div class="rule" style="left:582px;top:118px"></div>
  <svg class="abs" style="left:40px;top:262px" width="30" height="54"><path d="M27 2L3 27l24 25" stroke="#111" stroke-width="2" fill="none"/></svg>
  <svg class="abs" style="left:1130px;top:262px" width="30" height="54"><path d="M3 2l24 25L3 52" stroke="#111" stroke-width="2" fill="none"/></svg>
  <div class="svc svc-a" role="img" aria-label="Curtain-side truck on a mountain road">Lorem ipsum dolor</div>
  <div class="svc svc-b">
    <div class="panel">
      <svg width="98" height="70" viewBox="0 0 98 70" fill="none" stroke="#fff" stroke-width="3"><rect x="2" y="6" width="60" height="44"/><path d="M62 22h18l14 16v12H62z"/><circle cx="22" cy="56" r="8" fill="#9a0818"/><circle cx="78" cy="56" r="8" fill="#9a0818"/><path d="M8 2h40"/></svg>
      <h3>Lorem ipsum dolor</h3>
      <p>Lorem ipsum dolor sit amet, consectetur adipiscing elit, sed do eiusmod tempor incididunt ut labore et dolore</p>
    </div>
  </div>
  <div class="svc svc-c" role="img" aria-label="Two truck cabs parked in a yard">Lorem ipsum dolor</div>
</section>

<h2 class="sec-title" style="left:0;width:1200px;text-align:center;top:1902px">Our <span class="accent">Testimonials</span></h2>
<div class="rule" style="left:582px;top:1966px"></div>
<div class="tarrow" style="left:50px;background:#eee"><svg width="8" height="10"><path d="M7 0L0 5l7 5z" fill="#8b0a14"/></svg></div>
<div class="tarrow" style="left:1121px;background:var(--ruby)"><svg width="8" height="10"><path d="M1 0l7 5-7 5z" fill="#fff"/></svg></div>
<article class="tcard" style="left:123px">
  <div class="avatar"><i role="img" aria-label="Client portrait"></i></div>
  <div class="tname">Jhon Deo</div>
  <div class="trole">Lorem ipsum dolor consectetur adipiscing</div>
  <p class="tquote">Lorem ipsum dolor sit amet, consectetur adipiscing elit, sed do eiusmod tempor incididunt labore et dolore magna aliqua. enim ad minim veniam, quis nostrud exercitation ullamco laboris nisi ut aliquip commodo consequat.</p>
  <span class="tmore">Read More</span>
</article>
<article class="tcard" style="left:629px">
  <div class="avatar"><i role="img" aria-label="Client portrait"></i></div>
  <div class="tname">Jhon Deo</div>
  <div class="trole">Lorem ipsum dolor consectetur adipiscing</div>
  <p class="tquote">Lorem ipsum dolor sit amet, consectetur adipiscing elit, sed do eiusmod tempor incididunt labore et dolore magna aliqua. enim ad minim veniam, quis nostrud exercitation ullamco laboris nisi ut aliquip commodo consequat.</p>
  <span class="tmore">Read More</span>
</article>

<section class="abs quote" role="img" aria-label="Truck cab parked on a frosty yard">
  <svg class="abs" style="left:0;top:0" width="1200" height="616"><rect x="916" y="0" width="284" height="616" fill="#151213"/><polygon points="388,59 1200,59 1200,558 536,558" fill="rgba(95,12,36,0.94)"/></svg>
  <h2 class="sec-title" style="left:575px;top:101px;color:#fff">Request A Quote</h2>
  <div class="rule" style="left:575px;top:166px"></div>
  <div class="field" style="left:575px;top:200px;width:251px;height:44px">First Name *<svg viewBox="0 0 12 12"><circle cx="6" cy="3.5" r="3" fill="#777"/><path d="M0 12a6 5 0 0 1 12 0z" fill="#777"/></svg></div>
  <div class="field" style="left:834px;top:200px;width:253px;height:44px">Last Name *<svg viewBox="0 0 12 12"><circle cx="6" cy="3.5" r="3" fill="#777"/><path d="M0 12a6 5 0 0 1 12 0z" fill="#777"/></svg></div>
  <div class="field" style="left:575px;top:254px;width:251px;height:45px">Email Address *<svg viewBox="0 0 12 12"><rect x="0" y="2" width="12" height="9" fill="#777"/><path d="M0 2l6 5 6-5" stroke="#fff" fill="none"/></svg></div>
  <div class="field" style="left:834px;top:254px;width:253px;height:45px">Phone No *<svg viewBox="0 0 24 24"><path fill="#777" d="M6.6 10.8a15 15 0 0 0 6.6 6.6l2.2-2.2a1 1 0 0 1 1-.25 11.4 11.4 0 0 0 3.6.57 1 1 0 0 1 1 1V20a1 1 0 0 1-1 1A17 17 0 0 1 3 4a1 1 0 0 1 1-1h3.5a1 1 0 0 1 1 1c0 1.25.2 2.45.57 3.57a1 1 0 0 1-.25 1z"/></svg></div>
  <div class="field" style="left:575px;top:309px;width:512px;height:111px;align-items:flex-start">Your Message *<svg viewBox="0 0 12 12"><ellipse cx="6" cy="5" rx="5.5" ry="4" fill="none" stroke="#777"/></svg></div>
  <div class="btn" style="left:575px;top:452px;width:149px;height:48px;border:1px solid #fff">Submit Now <span class="dot"><svg viewBox="0 0 10 10"><path d="M3 1l4 4-4 4" stroke="#8b0a14" stroke-width="2" fill="none"/></svg></span></div>
</section>

<footer>
  <h3 class="fhead" style="left:123px">About Us</h3><div class="frule" style="left:123px"></div>
  <p class="ftext" style="left:123px;top:3156px;width:325px;text-align:justify">Lorem ipsum dolor sit consectetur adipiscing elit, sed do eiusmod tempor incididunt ut labore et dolore magna aliqua. Ut enim ad minim veniam, quis nostrud exercitation ullamco laboris nisi aliquip ex ea commodo consequat. Duis aute irure dolor in reprehenderit in voluptate velit.</p>

  <h3 class="fhead" style="left:544px">Contact Us</h3><div class="frule" style="left:544px"></div>
  <div class="fcontact" style="top:3159px"><span class="pin"><svg width="12" height="14" viewBox="0 0 12 16"><path d="M6 0a6 6 0 0 1 6 6c0 4-6 10-6 10S0 10 0 6a6 6 0 0 1 6-6z" fill="#fff"/><circle cx="6" cy="6" r="2" fill="#8b0a14"/></svg></span>253, Lorem ipsum dolor sit ameted</div>
  <div class="fcontact" style="top:3207px"><span class="pin"><svg width="13" height="13" viewBox="0 0 24 24"><path fill="#fff" d="M6.6 10.8a15 15 0 0 0 6.6 6.6l2.2-2.2a1 1 0 0 1 1-.25 11.4 11.4 0 0 0 3.6.57 1 1 0 0 1 1 1V20a1 1 0 0 1-1 1A17 17 0 0 1 3 4a1 1 0 0 1 1-1h3.5a1 1 0 0 1 1 1c0 1.25.2 2.45.57 3.57a1 1 0 0 1-.25 1z"/></svg></span>+1 555 010 4477</div>
  <div class="fcontact" style="top:3263px"><span class="pin"><svg width="13" height="11" viewBox="0 0 12 10"><rect width="12" height="10" fill="#fff"/><path d="M0 0l6 5 6-5" stroke="#8b0a14" fill="none"/></svg></span>info@garvelprycetransport.com</div>

  <h3 class="fhead" style="left:967px">Quick Links</h3><div class="frule" style="left:967px"></div>
  <ul class="qlinks"><li>Home</li><li>About Us</li><li>Our Services</li><li>Testimonials</li><li>Contact Us</li></ul>

  <div class="abs bottom-bar">
    <span class="bsoc" style="left:124px"><i></i></span>
    <span class="bsoc" style="left:166px"><i></i></span>
    <span class="bsoc" style="left:207px"><i></i></span>
    <span class="abs" style="right:112px;top:17px;color:#fff;font-size:14px">© 2024 Garvel Pryce Transport.All Rights Reserved</span>
  </div>
</footer>

</body>
</html>
```